Business Card Design

Business Card for professional consulting firm working with large financial institutions.

Target Market(s)

Executive buyers

Industry/Entity Type

Banking

Contact Information for Business Card

Mild creativity wanted. Not boring, but do elaborate artwork.

Font styles to use
Serif
Sans Serif

Colors

Designer to choose colors to be used in the design.

Requirements
Must have
• Standard business card features - company name, individual name, telephone, website, email, locations.
Nice to have
• Two colors
Should not have
• too many colors, fancy printing, cartoons.

```html
<!DOCTYPE html>
<html lang="en">
<head>
<meta charset="utf-8">
<title>northvale — Business Card</title>
<link rel="stylesheet" href="https://fonts.googleapis.com/css2?family=Tinos:wght@400;700&display=swap">
<style>
  :root {
    --bg: #dcd9d5;
    --ink-black: #0c0c0c;
    --gloss-mid: #3a3a3a;
    --paper: #f1f1f1;
    --swoosh: #bdbdbd;
    --text-light: #e6e6e6;
    --text-muted: #c4c4c4;
    --brand-dark: #1a1a1a;
  }
  * { margin: 0; padding: 0; box-sizing: border-box; }
  html, body { width: 1200px; height: 886px; overflow: hidden; }
  body {
    background: var(--bg);
    font-family: "Tinos", "Times New Roman", serif;
    display: flex;
    flex-direction: column;
    align-items: center;
    justify-content: center;
    gap: 60px;
  }
  .card {
    position: relative;
    width: 600px;
    height: 343px;
    border-radius: 16px;
    overflow: hidden;
    box-shadow: 0 10px 24px rgba(0,0,0,0.28);
  }
  .card--front {
    background: linear-gradient(100deg, var(--ink-black) 0%, var(--ink-black) 38%, var(--gloss-mid) 52%, #1b1b1b 62%, var(--ink-black) 100%);
    display: flex;
    align-items: center;
    justify-content: center;
  }
  .brand {
    display: flex;
    align-items: center;
    gap: 10px;
    font-family: "Tinos", "Times New Roman", serif;
    font-weight: 400;
    letter-spacing: 0.5px;
  }
  .brand__dot {
    width: 10px;
    height: 10px;
    border-radius: 50%;
  }
  .card--front .brand { font-size: 46px; color: var(--text-light); }
  .card--front .brand__dot { background: var(--text-light); }

  .card--back { background: var(--ink-black); }
  .card-back__art { position: absolute; inset: 0; }
  .contact {
    position: absolute;
    left: 40px;
    top: 44px;
    color: var(--text-muted);
    font-size: 14.5px;
    line-height: 1.2;
  }
  .contact__name { font-size: 24px; font-weight: 700; color: var(--text-light); letter-spacing: 0.5px; }
  .contact__title { font-size: 16px; color: var(--text-light); margin-bottom: 10px; }
  .contact__group { margin-bottom: 12px; }
  .card--back .brand {
    position: absolute;
    left: 385px;
    top: 190px;
    font-size: 30px;
    color: var(--brand-dark);
  }
  .card--back .brand__dot { background: var(--brand-dark); width: 8px; height: 8px; }
</style>
</head>
<body>
  <section class="card card--front" aria-label="Card front">
    <div class="brand"><span class="brand__name">northvale</span><span class="brand__dot"></span></div>
  </section>

  <section class="card card--back" aria-label="Card back">
    <svg class="card-back__art" width="600" height="343" viewBox="0 0 600 343" aria-hidden="true">
      <defs>
        <linearGradient id="back-gloss" x1="0" y1="0" x2="1" y2="0.3">
          <stop offset="0" stop-color="#0c0c0c"/>
          <stop offset="0.35" stop-color="#1a1a1a"/>
          <stop offset="0.5" stop-color="#3a3a3a"/>
          <stop offset="0.6" stop-color="#151515"/>
          <stop offset="1" stop-color="#0c0c0c"/>
        </linearGradient>
      </defs>
      <rect width="600" height="343" fill="url(#back-gloss)"/>
      <path d="M352 0 C 300 80, 262 200, 256 343 L600 343 L600 0 Z" fill="var(--swoosh)"/>
      <path d="M362 0 C 314 80, 276 200, 268 343 L600 343 L600 0 Z" fill="var(--paper)"/>
    </svg>
    <div class="contact">
      <div class="contact__name">Daniel Hart</div>
      <div class="contact__title">Managing Director</div>
      <div class="contact__group">
        <div>northvale</div>
        <div>2140 Harbor View Road</div>
        <div>Cedar Point, Ohio 40218</div>
      </div>
      <div>555 210 4836</div>
      <div>info@northvale.com</div>
      <div>www.northvale.com</div>
    </div>
    <div class="brand"><span class="brand__name">northvale</span><span class="brand__dot"></span></div>
  </section>
</body>
</html>
```